New Innovative Counselling and psychotherapy Service needs Business Card design

Keep it simple and professional. On one side, just company name and logo (perhaps in all blue) and maybe a tag line.

On other side (all white) my name and Qualifications in centre

Industry/Entity Type

Health And Wellness

Contact Information for Business Card

Dara Whelby
Counsellor & Psychotherapist
BSc (Psychol.), BA, Dip. (Couns. & Psych.), PG.Cert (CBT), FGTrK, ONRE

I will also require Mobile no, Email and web site address of which I'll pass on to final designer.

Font styles to use
Sans Serif

Requirements
Must have
• My Logo Only and please use the colours in logo that is in it.
Should not have
• Any other images

```html
<!DOCTYPE html>
<html lang="en">
<head>
<meta charset="utf-8">
<title>Brightwell Lane — Business Card</title>
<link href="https://fonts.googleapis.com/css2?family=Questrial&family=Roboto:wght@400;700&display=swap" rel="stylesheet">
<style>
  :root {
    --page-bg: #e8e9eb;
    --card-white: #ffffff;
    --brand-blue: #3fa6e0;
    --brand-teal: #62bcc0;
    --brand-green: #8ccc5e;
    --ink-dark: #2e2e30;
    --ink-text: #3a3a3c;
    --name-blue: #3a9ad8;
  }
  * { box-sizing: border-box; margin: 0; padding: 0; }
  html, body { width: 1200px; height: 726px; overflow: hidden; }
  body {
    background: var(--page-bg);
    position: relative;
    font-family: "Roboto", Arial, sans-serif;
  }
  .card {
    position: absolute;
    top: 213px;
    width: 525px;
    height: 300px;
    overflow: hidden;
    box-shadow: 0 6px 18px rgba(0,0,0,0.12);
  }
  .card-front {
    left: 50px;
    background: linear-gradient(110deg, var(--brand-blue) 0%, var(--brand-teal) 45%, #9fd9a0 75%, var(--brand-green) 100%);
    display: flex;
    align-items: center;
    justify-content: center;
  }
  .front-wordmark {
    font-family: "Questrial", Arial, sans-serif;
    color: var(--card-white);
    font-size: 46px;
    letter-spacing: 1px;
  }
  .card-back { left: 625px; background: var(--card-white); }
  .back-wave { position: absolute; inset: 0; width: 100%; height: 100%; }
  .brand-lockup {
    position: absolute;
    left: 36px;
    top: 108px;
    display: flex;
    align-items: center;
    gap: 14px;
  }
  .brand-dot {
    width: 52px; height: 52px;
    border-radius: 50%;
    background: var(--brand-blue);
  }
  .brand-name {
    font-family: "Questrial", Arial, sans-serif;
    font-size: 36px;
    color: var(--ink-dark);
  }
  .holder {
    position: absolute;
    left: 38px;
    top: 190px;
    color: var(--ink-text);
    font-size: 11.5px;
    line-height: 1.35;
  }
  .holder-name {
    color: var(--name-blue);
    font-weight: 700;
    font-size: 21px;
    line-height: 1.1;
    margin-bottom: 2px;
  }
  .contact {
    position: absolute;
    right: 22px;
    top: 178px;
    list-style: none;
    text-align: right;
    color: var(--card-white);
    font-size: 11.5px;
    line-height: 1.7;
  }
  .contact li { display: flex; justify-content: flex-end; align-items: center; gap: 6px; }
  .contact svg { width: 10px; height: 10px; }
</style>
</head>
<body>
  <section class="card card-front">
    <div class="front-wordmark">Brightwell Lane</div>
  </section>

  <section class="card card-back">
    <svg class="back-wave" viewBox="0 0 525 300" preserveAspectRatio="none" aria-hidden="true">
      <path d="M110,300 C240,290 290,190 350,160 C410,132 470,125 525,118 L525,131 C470,138 420,142 362,168 C302,196 255,296 135,300 Z" fill="var(--brand-green)"/>
      <path d="M150,300 C262,300 302,202 364,178 C424,154 470,150 525,144 L525,300 Z" fill="var(--brand-blue)"/>
      <path d="M0,283 C90,292 170,290 230,270 L235,274 C170,296 90,298 0,292 Z" fill="var(--brand-green)"/>
      <path d="M0,292 C90,298 170,296 235,274 C215,290 190,300 150,300 L0,300 Z" fill="var(--brand-blue)"/>
    </svg>

    <div class="brand-lockup">
      <span class="brand-dot"></span>
      <span class="brand-name">Brightwell Lane</span>
    </div>

    <div class="holder">
      <div class="holder-name">Dara Whelby</div>
      <div>Counsellor &amp; Psychotherapist</div>
      <div>BSc (Psychol.), BA, Dip. (Couns. &amp; Psych.),</div>
      <div>PG.Cert (CBT), FGTrK, ONRE</div>
    </div>

    <ul class="contact">
      <li>0987 654 3210
        <svg viewBox="0 0 10 10"><path d="M1,3 Q5,0 9,3 L8,4.5 L6.5,3.8 L6.5,3 Q5,2.5 3.5,3 L3.5,3.8 L2,4.5 Z M2.5,5.5 H7.5 L8.5,9 H1.5 Z" fill="#fff"/></svg>
      </li>
      <li>www.BrightwellLane.com
        <svg viewBox="0 0 10 10"><rect x="0.5" y="2" width="9" height="6" fill="#fff"/><path d="M0.5,2 L5,5.5 L9.5,2" stroke="var(--brand-blue)" stroke-width="0.8" fill="none"/></svg>
      </li>
      <li>dara.w@BrightwellLane.com
        <svg viewBox="0 0 10 10"><circle cx="5" cy="5" r="4.3" fill="none" stroke="#fff" stroke-width="1"/><path d="M0.7,5 H9.3 M5,0.7 C2.5,3 2.5,7 5,9.3 M5,0.7 C7.5,3 7.5,7 5,9.3" stroke="#fff" stroke-width="0.8" fill="none"/></svg>
      </li>
    </ul>
  </section>
</body>
</html>
```